Brivolt Technologies business card design

We need a business card designed with our new logo. it would be great if the card could communicate it is a technology based company.

Target Market(s)

system integrators

Industry/Entity Type

technology, IOT

Contact Information for Business Card

Name, designation, Address, telephone number, email address

Requirements
Must have
• logo and company name
Nice to have
• something to do with technology

```html
<!DOCTYPE html>
<html lang="en">
<head>
<meta charset="utf-8">
<title>Brivolt Technologies – Business Card</title>
<link href="https://fonts.googleapis.com/css2?family=Open+Sans:wght@400;600;700&display=swap" rel="stylesheet">
<style>
  :root {
    --backdrop: #3b3b3b;
    --card: #161616;
    --accent: #f7941d;
    --ink: #f2f2f2;
    --ink-soft: #d8d8d8;
    --emboss: #2a2a2a;
  }
  * { box-sizing: border-box; margin: 0; padding: 0; }
  html, body { width: 1200px; height: 801px; overflow: hidden; }
  body {
    background: var(--backdrop);
    font-family: "Open Sans", Arial, sans-serif;
    position: relative;
  }
  .card {
    position: absolute;
    top: 252px;
    width: 530px;
    height: 298px;
    background: var(--card);
    border-left: 2px solid var(--accent);
    border-bottom: 2px solid var(--accent);
    box-shadow: 0 14px 30px rgba(0,0,0,0.45);
  }
  .card--front { left: 55px; }
  .card--back { left: 615px; }

  .brand {
    position: absolute;
    top: 36px;
    right: 34px;
    display: flex;
    align-items: center;
    gap: 10px;
    color: var(--ink);
    font-weight: 700;
    font-size: 24px;
    letter-spacing: 1px;
    text-transform: uppercase;
  }
  .brand__square { width: 22px; height: 22px; background: var(--accent); }

  .divider {
    position: absolute;
    top: 110px;
    left: 150px;
    right: 30px;
    height: 1px;
    background: var(--accent);
  }

  .person { position: absolute; left: 30px; top: 142px; }
  .person__name {
    color: var(--accent);
    font-weight: 700;
    font-size: 19px;
    text-transform: uppercase;
    letter-spacing: 0.3px;
  }
  .person__role { color: var(--ink-soft); font-size: 13px; margin-top: 1px; }
  .person__rule { width: 150px; height: 1px; background: var(--accent); margin: 12px 0 12px; }

  .contacts { list-style: none; }
  .contacts li {
    display: flex;
    align-items: center;
    gap: 8px;
    color: var(--ink);
    font-size: 12.5px;
    line-height: 20px;
  }
  .contacts svg { width: 11px; height: 11px; fill: var(--accent); flex: none; }

  .address {
    position: absolute;
    right: 30px;
    top: 135px;
    text-align: right;
    color: var(--ink);
    font-size: 13px;
    line-height: 19px;
  }

  .back-brand {
    position: absolute;
    left: 0; right: 0; top: 50%;
    transform: translateY(-50%);
    display: flex;
    justify-content: center;
    align-items: center;
    gap: 16px;
    color: var(--emboss);
    font-weight: 700;
    font-size: 36px;
    letter-spacing: 2px;
    text-transform: uppercase;
  }
  .back-brand__square { width: 34px; height: 34px; background: var(--emboss); }
</style>
</head>
<body>
  <section class="card card--front" aria-label="Business card front">
    <div class="brand"><span class="brand__square"></span>Brivolt Technologies</div>
    <div class="divider"></div>

    <div class="person">
      <p class="person__name">Dane Corwell</p>
      <p class="person__role">President</p>
      <div class="person__rule"></div>
      <ul class="contacts">
        <li><svg viewBox="0 0 24 24" aria-hidden="true"><path d="M6.6 10.8a15.1 15.1 0 0 0 6.6 6.6l2.2-2.2a1 1 0 0 1 1-.25 11.4 11.4 0 0 0 3.6.57 1 1 0 0 1 1 1V20a1 1 0 0 1-1 1A17 17 0 0 1 3 4a1 1 0 0 1 1-1h3.5a1 1 0 0 1 1 1c0 1.25.2 2.45.57 3.6a1 1 0 0 1-.25 1z"/></svg>555-018-4427</li>
        <li><svg viewBox="0 0 24 24" aria-hidden="true"><path d="M2 5h20v14H2z M2 5l10 8 10-8" /></svg>info@brivolttechnologies.com</li>
        <li><svg viewBox="0 0 24 24" aria-hidden="true"><circle cx="12" cy="12" r="10"/></svg>www.brivolttechnologies.com</li>
      </ul>
    </div>

    <address class="address" style="font-style:normal">
      1870 Lantern Cove Road<br>
      Seacliff CA 90418
    </address>
  </section>

  <section class="card card--back" aria-label="Business card back">
    <div class="back-brand"><span class="back-brand__square"></span>Brivolt Technologies</div>
  </section>
</body>
</html>
```